Create a banner for me that embodies my health and well being package.

I am an intuitive counselor with a busy practice helping clients to shift their blocks and move forward in their lives.
I have created a package called '9 paths home again'
I am wanting a banner to put on my website page, facebook page and to use as a letter head in mailouts.
My ideal clients are those who want to create change in their lives and who invest money in themselves and their personal and spiritual growth.
I am different to regular life coaches as my sessions have a spiritual twist to them creating much deeper change in my clients.
I would like the banner to be mainly font with the title of the progam: 9 Paths Home Again (no other wording) (something along the lines of the Blackjack font) and that ties in with the theme of my website. I'm not sure what else I want with it and am looking for ideas.
Website:
www.lumorawellspring.com.au
I also have a current facebook page for the business:
https://www.facebook.com/Lumora-Wellspring-Studio-502718364091557/
(Note: I am about to drop my logo and business name and move to using my own name - the rest of the website will remain the same).
I have attached a doc with the draft of what wording will be on the website page any advertising will link to, to give you an idea of what the program is about.

Target Market(s)

People who invest money on themselves who are looking to improve their emotional well being and creating change in their life. Majority are middle aged women (also younger females and some men)

Industry/Entity Type

Health And Wellness

Font styles to use
Other font styles liked:
• I like Blackjack and Amienne. Along those lines.

Requirements
Must have
• Attractive, modern and GREAT font.
Nice to have
• Surprise me with something amazing!
• I love the colours in the 2 images I have up loaded as they represent the heart chakra colours. They could be a feature on the banner or blurred into the background.
Should not have
• Even though my work is quite spiritual I don't want it to look woo woo (meaning airy fairy spiritual stuff!)

```html
<!DOCTYPE html>
<html lang="en">
<head>
<meta charset="utf-8">
<title>9 Paths Home Again – Banner</title>
<link href="https://fonts.googleapis.com/css2?family=Allura&display=swap" rel="stylesheet">
<style>
  :root {
    --tone-teal-soft: #8fa7a4;
    --tone-blush: #d9ada0;
    --tone-sea: #5fa6b2;
    --tone-sea-deep: #4a93a2;
    --ink: #111111;
  }

  * { margin: 0; padding: 0; box-sizing: border-box; }

  html, body {
    width: 1200px;
    height: 452px;
    overflow: hidden;
    background: #ffffff;
  }

  .banner {
    position: relative;
    width: 1200px;
    height: 452px;
    overflow: hidden;
  }

  .banner__photo {
    position: absolute;
    inset: 0;
    background: linear-gradient(180deg,
      var(--tone-teal-soft) 0%,
      var(--tone-blush) 40%,
      var(--tone-sea) 72%,
      var(--tone-sea-deep) 100%);
  }

  .banner__title {
    position: absolute;
    left: 575px;
    top: 134px;
    width: 568px;
    height: 160px;
    border-left: 2px solid var(--ink);
    border-right: 2px solid var(--ink);
  }

  .banner__heading {
    position: absolute;
    left: 0;
    top: -66px;
    width: 100%;
    font-family: "Allura", cursive;
    font-weight: 400;
    color: var(--ink);
    text-align: center;
    font-size: 132px;
    line-height: 114px;
    letter-spacing: 1px;
  }

  .banner__heading-line {
    display: block;
    white-space: nowrap;
  }
</style>
</head>
<body>
  <main class="banner">
    <div class="banner__photo" role="img" aria-label="Photograph of a woman walking barefoot along a beach at sunset, waves rolling in under a hazy pink and teal sky"></div>

    <div class="banner__title">
      <h1 class="banner__heading">
        <span class="banner__heading-line">9 paths</span>
        <span class="banner__heading-line">home again</span>
      </h1>
    </div>
  </main>
</body>
</html>
```